Brightmoor Talent company

We require a website for job recruitment company called "Brightmoor Talent"
Our company is specialising in recruitment of skilled labour from Sri Lanka into Australian market.
We would like to include a job advertising plugin where jobs can be listed and applied for .
COPYWRITING MUST BE INCLUDED !

Industry/Entity Type

Recruitment

Coding

Coded - Design and coding required

Number of Pages Required

5+ page

Colors

Designer to choose colors to be used in the design.

```html
<!DOCTYPE html>
<html lang="en">
<head>
<meta charset="utf-8">
<title>Brightmoor Talent – Recruitment</title>
<link href="https://fonts.googleapis.com/css2?family=Merriweather:wght@400;700;900&family=Roboto:wght@400;500;700&display=swap" rel="stylesheet">
<style>
:root{
  --blue:#0b4fa3;
  --blue-dark:#083a7a;
  --blue-soft:#8fb3df;
  --blue-pale:#e6eef8;
  --ink:#222;
  --muted:#666;
  --white:#fff;
  --line:#d9dde3;
}
*{box-sizing:border-box;margin:0;padding:0}
html,body{width:1200px;height:5260px;overflow:hidden}
body{position:relative;font-family:"Roboto",Arial,sans-serif;color:var(--ink);background:var(--white)}
.abs{position:absolute}
.serif{font-family:"Merriweather",Georgia,serif}
.brand{font-family:"Merriweather",Georgia,serif;font-weight:900;color:var(--blue);line-height:1.05}
.section-title{position:absolute;left:0;width:1200px;text-align:center;font-family:"Merriweather",Georgia,serif;font-weight:700;font-size:31px;color:var(--blue);letter-spacing:.5px}
.section-title.light{color:var(--white)}

/* header */
.site-header{position:absolute;left:0;top:0;width:1200px;height:98px;background:var(--white);box-shadow:0 2px 6px rgba(0,0,0,.08);z-index:3}
.site-header .brand{position:absolute;left:171px;top:22px;font-size:30px;width:230px}
.hdr-btn{position:absolute;top:12px;height:37px;font-size:11px;font-weight:700;display:flex;align-items:center;justify-content:center;border-radius:3px}
.hdr-btn.outline{left:812px;width:111px;border:1.5px solid var(--ink);color:var(--ink)}
.hdr-btn.solid{left:933px;width:94px;background:var(--blue);color:var(--white)}
.main-nav{position:absolute;right:173px;top:64px;display:flex;gap:28px;font-size:13px;font-weight:500}

/* hero */
.hero-photo{position:absolute;left:0;top:98px;width:1200px;height:620px;background:linear-gradient(100deg,#3b4d66 0%,#6a7e98 35%,#c9d2dc 62%,#f1f3f6 80%,#fafafa 100%)}
.hero-curve{position:absolute;left:0;top:560px}
.hero-brand{position:absolute;right:173px;top:176px;text-align:right;font-size:58px;width:560px}
.hero-tag{position:absolute;right:173px;top:356px;text-align:right;font-family:"Merriweather",Georgia,serif;font-weight:700;font-size:27px;line-height:1.4;color:#111}
.hero-arrows{position:absolute;left:916px;top:488px}

/* intro band */
.intro-band{position:absolute;left:0;top:810px;width:1200px;height:552px;background:var(--blue)}
.intro-col{position:absolute;top:90px;width:340px;text-align:center;color:var(--white)}
.intro-col h3{font-family:"Merriweather",Georgia,serif;font-size:21px;font-weight:700;margin:28px 0 18px}
.intro-col p{font-size:12.5px;line-height:1.7}
.intro-cta{position:absolute;left:366px;top:448px;width:468px;height:40px;background:var(--white);color:var(--ink);font-size:13px;font-weight:500;display:flex;align-items:center;justify-content:center;border-radius:3px}

/* process */
.process-label{position:absolute;font-family:"Merriweather",Georgia,serif;font-weight:700;font-size:20px;line-height:1.25;color:var(--blue)}

/* industry */
.industry-band{position:absolute;left:0;top:2056px;width:1200px;height:378px;background:var(--blue)}
.industry{position:absolute;top:158px;width:180px;text-align:center;color:var(--white)}
.industry h4{font-size:15px;font-weight:500;margin-top:14px;letter-spacing:.3px}
.industry span{display:block;font-size:13px;margin-top:8px}

/* recent jobs */
.job-card{position:absolute;left:171px;width:856px;height:137px;background:var(--white);box-shadow:0 2px 10px rgba(0,0,0,.14)}
.job-card.featured{box-shadow:0 3px 14px rgba(0,0,0,.35)}
.job-logo{position:absolute;top:10px;width:114px;height:117px;border:1.5px solid #555;border-radius:4px;display:flex;align-items:center;justify-content:center;gap:6px;font-weight:700;font-size:14px;color:var(--ink)}
.job-logo i{display:inline-block;width:12px;height:12px;background:var(--ink);border-radius:50%}
.job-title{position:absolute;top:24px;font-size:15px;font-weight:500;letter-spacing:.3px}
.job-meta{position:absolute;top:56px;font-size:12.5px;display:flex;gap:22px}
.job-meta span{display:flex;align-items:center;gap:6px}
.job-desc{position:absolute;top:82px;width:540px;font-size:11.5px;color:var(--muted);line-height:1.5}
.btn-outline{position:absolute;top:47px;width:102px;height:40px;border:1.5px solid var(--blue);color:var(--blue);font-family:"Merriweather",Georgia,serif;font-weight:700;font-size:11px;display:flex;align-items:center;justify-content:center;border-radius:3px}
.btn-solid{background:var(--blue);color:var(--white);font-family:"Merriweather",Georgia,serif;font-weight:700;font-size:11px;display:flex;align-items:center;justify-content:center;border-radius:3px}

/* why choose */
.why{position:absolute;left:0;top:3134px;width:1200px;height:527px;background:#f7f8fa}
.why-photo{position:absolute;left:0;top:0;width:640px;height:527px;background:linear-gradient(120deg,#123a70,#2a5c9c 55%,#1a4886)}
.why-title{position:absolute;left:680px;top:78px;font-family:"Merriweather",Georgia,serif;font-weight:700;font-size:31px;color:var(--blue)}
.acc-item{position:absolute;left:680px;width:347px;height:43px;border:1.5px solid #555;background:var(--white);font-size:13px;font-weight:500;display:flex;align-items:center;justify-content:space-between;padding:0 12px}
.acc-item b{font-size:20px;font-weight:400}
.acc-body{position:absolute;left:680px;top:206px;width:347px;font-size:11px;color:var(--muted);line-height:1.65}

/* testimonials */
.quote-card{position:absolute;top:3865px;width:421px;height:335px;background:var(--white);box-shadow:0 2px 12px rgba(0,0,0,.14);text-align:center}
.avatar{position:absolute;left:157px;top:44px;width:106px;height:106px;border-radius:50%;border:2px solid #333;background:radial-gradient(circle at 50% 40%,#c9a68a,#6b5445 70%,#3a3a3a)}
.quote-card p{position:absolute;left:24px;top:188px;width:373px;font-size:12px;color:var(--muted);line-height:1.6}
.quote-card h5{position:absolute;left:0;top:294px;width:421px;font-family:"Merriweather",Georgia,serif;font-size:14px;color:var(--blue);font-weight:700}

/* blog */
.blog-card{position:absolute;top:4384px;width:278px;height:394px;background:var(--white);box-shadow:0 2px 12px rgba(0,0,0,.2);text-align:center}
.blog-img{width:278px;height:196px;background:linear-gradient(135deg,#5b6b80,#c9cfd8 50%,#8896a8)}
.blog-card h4{font-family:"Merriweather",Georgia,serif;font-size:18px;font-weight:700;margin-top:24px}
.blog-card p{font-size:12px;color:var(--muted);line-height:1.6;margin:12px 20px 0}
.blog-card .btn-solid{position:absolute;left:91px;top:330px;width:96px;height:41px}

/* footer */
.footer .brand{position:absolute;left:171px;top:5000px;font-size:34px;width:240px}
.foot-col{position:absolute;top:4940px}
.foot-col h6{font-family:"Merriweather",Georgia,serif;font-size:18px;font-weight:700;margin-bottom:14px}
.post{margin-bottom:10px;width:200px}
.post b{display:block;font-size:11.5px;font-weight:500;line-height:1.35}
.post span{font-size:10.5px;color:var(--muted)}
.links li{list-style:none;font-size:12px;margin-bottom:10px}
.contact-row{display:flex;gap:12px;margin-bottom:16px;font-size:11.5px;font-weight:500;line-height:1.4;width:210px}
.contact-row i{flex:none;width:28px;height:28px;border-radius:50%;border:2px solid var(--blue);display:flex;align-items:center;justify-content:center}
.copyright{position:absolute;left:0;top:5197px;width:1200px;height:63px;background:var(--blue);color:var(--white);font-size:13px;font-weight:500;display:flex;align-items:center;justify-content:center}
</style>
</head>
<body>

<header class="site-header">
  <div class="brand">Brightmoor<br>Talent</div>
  <a class="hdr-btn outline">BROWSE JOBS</a>
  <a class="hdr-btn solid">POST A JOB</a>
  <nav class="main-nav"><span>HOME</span><span>ABOUT</span><span>BLOG</span><span>SERVICES</span><span>BLOG</span><span>CONTACT</span></nav>
</header>

<section class="hero">
  <div class="hero-photo" role="img" aria-label="Photo of two professionals shaking hands in a bright meeting room"></div>
  <svg class="hero-curve" width="1200" height="260" viewBox="0 0 1200 260">
    <path d="M0 110 C360 250 820 230 1200 40 L1200 260 L0 260Z" fill="#0b4fa3"/>
    <path d="M0 110 C360 250 820 230 1200 40 L1200 70 C820 250 380 260 0 140Z" fill="#ffffff" opacity=".9"/>
  </svg>
  <div class="brand hero-brand">Brightmoor<br>Talent</div>
  <div class="hero-tag">Find the Most Exciting<br>Jobs here...</div>
  <svg class="hero-arrows" width="112" height="80" viewBox="0 0 112 80" fill="none" stroke="#fff" stroke-width="3">
    <polyline points="38,4 4,40 38,76"/><polyline points="74,4 108,40 74,76"/>
  </svg>
</section>

<section class="intro-band">
  <div class="intro-col" style="left:157px">
    <svg width="110" height="110" viewBox="0 0 110 110" fill="none" stroke="#fff" stroke-width="4">
      <rect x="10" y="30" width="80" height="58" rx="6"/><path d="M36 30V18h28v12M10 54h80"/><circle cx="78" cy="80" r="14" fill="#0b4fa3"/><path d="M88 90l14 14"/>
    </svg>
    <h3>LOOKING FOR A JOB?</h3>
    <p>Our ability to match the right employee with the right employer has helped many candidates in making life changing move to Australia and to become PERMANENT RESIDENT of Australia.</p>
  </div>
  <div class="intro-col" style="left:690px">
    <svg width="110" height="110" viewBox="0 0 110 110" fill="none" stroke="#fff" stroke-width="4">
      <circle cx="40" cy="34" r="16"/><circle cx="72" cy="34" r="16"/><path d="M10 100c0-24 14-36 30-36s30 12 30 36M42 100c0-24 14-36 30-36s30 12 30 36"/>
    </svg>
    <h3>LOOKING FOR EMPLOYEES?</h3>
    <p>We know, how difficult it is to get the skilled labour force to help with business growth and expansion. That is why we search, screen and select only the best suitable candidates with all documents ready to apply for visa which will dramatically save your time and money.</p>
  </div>
  <a class="intro-cta">CALL US TODAY AND LET US HELP YOU EXPAND YOUR BUSINESS</a>
</section>

<section class="process">
  <h2 class="section-title" style="top:1430px">OUR JOB HIRING PROCESS</h2>
  <svg class="abs" style="left:380px;top:1495px" width="440" height="440" viewBox="0 0 440 440">
    <circle cx="220" cy="220" r="184" fill="none" stroke="#0b4fa3" stroke-width="2"/>
    <circle cx="220" cy="220" r="140" fill="#8fb3df"/>
    <circle cx="220" cy="220" r="126" fill="#0b4fa3"/>
    <g fill="#0b4fa3" stroke="#fff" stroke-width="3">
      <circle cx="49" cy="145" r="38"/><circle cx="388" cy="145" r="38"/>
      <circle cx="61" cy="306" r="38"/><circle cx="378" cy="306" r="38"/>
      <circle cx="218" cy="400" r="38"/>
    </g>
    <g fill="none" stroke="#fff" stroke-width="2.5">
      <path d="M34 138h10l16-10v34l-16-10H34z"/>
      <circle cx="388" cy="145" r="14"/>
      <rect x="50" y="292" width="22" height="28" rx="2"/><path d="M55 300h12M55 307h12M55 314h8"/>
      <circle cx="378" cy="298" r="8"/><path d="M362 322c0-10 7-15 16-15s16 5 16 15"/>
      <rect x="206" y="386" width="24" height="30" rx="2"/><path d="M212 404l5 5 8-10"/>
    </g>
  </svg>
  <div class="process-label" style="right:822px;top:1614px;text-align:right">ADVERTISE<br>FOR JOB</div>
  <div class="process-label" style="left:823px;top:1614px">ORGANISE JOB<br>INTERVIEWS</div>
  <div class="process-label" style="right:814px;top:1778px;text-align:right">COLLECTING<br>APPLICATIONS</div>
  <div class="process-label" style="left:813px;top:1778px">SHORTLIST<br>CANDIDATES</div>
  <div class="process-label" style="left:0;width:1200px;top:1942px;text-align:center">REVIEWING THE<br>SUITABLE CANDIDATES</div>
</section>

<section class="industry-band">
  <h2 class="section-title light" style="top:66px">JOBS BY INDUSTRY</h2>
  <div class="industry" style="left:141px">
    <svg width="76" height="76" viewBox="0 0 76 76" fill="none" stroke="#fff" stroke-width="2.5"><rect x="10" y="8" width="44" height="58" rx="3"/><rect x="36" y="36" width="32" height="32" rx="2"/><path d="M42 44h20M42 52h20M42 60h20M18 20h28"/><circle cx="24" cy="46" r="8"/></svg>
    <h4>ACCOUNTING</h4><span>10 Positions</span>
  </div>
  <div class="industry" style="left:329px">
    <svg width="76" height="76" viewBox="0 0 76 76" fill="none" stroke="#fff" stroke-width="2.5"><rect x="14" y="6" width="34" height="62" rx="4"/><path d="M36 40l18-10v26l-18-10z M54 36h10 M58 24l8-6 M58 50l8 6"/></svg>
    <h4>DIGITAL</h4><span>2 Postitions</span>
  </div>
  <div class="industry" style="left:525px">
    <svg width="76" height="76" viewBox="0 0 76 76" fill="none" stroke="#fff" stroke-width="2.5"><path d="M8 26L38 8l30 18z M12 30h52 M18 34v26 M32 34v26 M44 34v26 M58 34v26 M8 64h60"/></svg>
    <h4>BANKING</h4><span>11 Postitions</span>
  </div>
  <div class="industry" style="left:710px">
    <svg width="76" height="76" viewBox="0 0 76 76" fill="none" stroke="#fff" stroke-width="2.5"><circle cx="38" cy="16" r="9"/><path d="M10 48l8-14h40l8 14v14H10z M10 48h56"/><circle cx="22" cy="56" r="4"/><circle cx="54" cy="56" r="4"/></svg>
    <h4>AUTOMOTIVE</h4><span>20 Positions</span>
  </div>
  <div class="industry" style="left:894px">
    <svg width="76" height="76" viewBox="0 0 76 76" fill="none" stroke="#fff" stroke-width="2.5"><rect x="8" y="14" width="58" height="40" rx="3"/><path d="M30 66h16M38 54v12M28 44l26-26 6 6-26 26-8 2z"/></svg>
    <h4>DESIGN</h4><span>15 Positions</span>
  </div>
</section>

<section class="recent-jobs">
  <h2 class="section-title" style="top:2504px">RECENT JOBS</h2>

  <article class="job-card" style="top:2597px">
    <div class="job-logo" style="left:9px"><i></i>Northgate</div>
    <div class="job-title" style="left:137px">SALES AND MARKETING COORDINATOR</div>
    <div class="job-meta" style="left:137px">
      <span><svg width="12" height="12" viewBox="0 0 12 12" fill="none" stroke="#222" stroke-width="1.3"><path d="M6 11s4-4 4-6.5a4 4 0 0 0-8 0C2 7 6 11 6 11z"/><circle cx="6" cy="4.5" r="1.4"/></svg>Australia</span>
      <span><svg width="12" height="12" viewBox="0 0 12 12" fill="none" stroke="#222" stroke-width="1.3"><circle cx="6" cy="6" r="5"/><path d="M1 6h10M6 1c2 2 2 8 0 10M6 1c-2 2-2 8 0 10"/></svg>Full Time</span>
    </div>
    <p class="job-desc" style="left:137px">Duis aute irure dolor in reprehenderit in voluptate velit esse cillum dolore eu fugiat nulla pariatur. Excepteur sint occaecat cupidatat non proident.</p>
    <a class="btn-outline" style="left:734px">VIEW MORE</a>
  </article>

  <article class="job-card featured" style="top:2753px">
    <a class="btn-solid" style="position:absolute;left:23px;top:48px;width:98px;height:40px">VIEW MORE</a>
    <div class="job-title" style="right:137px">CAR TRANSPORTER</div>
    <div class="job-meta" style="right:137px">
      <span>Full Time <svg width="12" height="12" viewBox="0 0 12 12" fill="none" stroke="#222" stroke-width="1.3"><circle cx="6" cy="6" r="5"/><path d="M1 6h10M6 1c2 2 2 8 0 10M6 1c-2 2-2 8 0 10"/></svg></span>
      <span>Australia <svg width="12" height="12" viewBox="0 0 12 12" fill="none" stroke="#222" stroke-width="1.3"><path d="M6 11s4-4 4-6.5a4 4 0 0 0-8 0C2 7 6 11 6 11z"/><circle cx="6" cy="4.5" r="1.4"/></svg></span>
    </div>
    <p class="job-desc" style="right:137px;text-align:right">Duis aute irure dolor in reprehenderit in voluptate velit esse cillum dolore eu fugiat nulla pariatur. Excepteur sint occaecat cupidatat non proident.</p>
    <div class="job-logo" style="right:9px"><i></i>Keelrow</div>
  </article>

  <article class="job-card" style="top:2920px">
    <div class="job-logo" style="left:9px"><i></i>Ashvale</div>
    <div class="job-title" style="left:137px">ELECTRONICS TECHNICIAN</div>
    <div class="job-meta" style="left:137px">
      <span><svg width="12" height="12" viewBox="0 0 12 12" fill="none" stroke="#222" stroke-width="1.3"><path d="M6 11s4-4 4-6.5a4 4 0 0 0-8 0C2 7 6 11 6 11z"/><circle cx="6" cy="4.5" r="1.4"/></svg>Australia</span>
      <span><svg width="12" height="12" viewBox="0 0 12 12" fill="none" stroke="#222" stroke-width="1.3"><circle cx="6" cy="6" r="5"/><path d="M1 6h10M6 1c2 2 2 8 0 10M6 1c-2 2-2 8 0 10"/></svg>Full Time</span>
    </div>
    <p class="job-desc" style="left:137px">Duis aute irure dolor in reprehenderit in voluptate velit esse cillum dolore eu fugiat nulla pariatur. Excepteur sint occaecat cupidatat non proident.</p>
    <a class="btn-outline" style="left:734px">VIEW MORE</a>
  </article>
</section>

<section class="why">
  <div class="why-photo" role="img" aria-label="Photo of a businessman reviewing documents, tinted blue"></div>
  <h2 class="why-title">WHY CHOOSE US</h2>
  <div class="acc-item" style="top:148px">Nemo enim ipsam voluptatem?<b>&#8211;</b></div>
  <p class="acc-body">Aliquam sapien est, mollis id mattis id, scelerisque sed dolor. Proin accumsan erat sem, id porta risus dignissim ac. Vestibulum nec sapien in lacus ornare nec nec justo.</p>
  <div class="acc-item" style="top:282px">Enim ad minima veniam?<b>+</b></div>
  <div class="acc-item" style="top:344px">Sed ut perspiciatis unde omnis?<b>+</b></div>
  <div class="acc-item" style="top:403px">Quis autem vel eum iure reprehenderit?<b>+</b></div>
</section>

<section class="clients">
  <h2 class="section-title" style="top:3744px">WORDS FROM OUR CLIENTS</h2>
  <svg class="abs" style="left:0;top:3990px" width="1200" height="880" viewBox="0 0 1200 880">
    <path d="M0 10 Q600 -40 1200 10 L1200 880 L0 880Z" fill="#0b4fa3"/>
  </svg>
  <article class="quote-card" style="left:171px">
    <div class="avatar" role="img" aria-label="Portrait of client Daniel Whitford"></div>
    <p>Nemo enim ipsam voluptatem quia voluptas sit aspernatur aut odit aut fugit, sed quia consequuntur magni dolores eos qui ratio ne voluptatem sequi nesciunt. Neque porro quisquam est, qui dolorem ipsum quia dolor sit amet, consectetur</p>
    <h5>- Daniel Whitford</h5>
  </article>
  <article class="quote-card" style="left:606px">
    <div class="avatar" role="img" aria-label="Portrait of client Owen Calloway"></div>
    <p>Nemo enim ipsam voluptatem quia voluptas sit aspernatur aut odit aut fugit, sed quia consequuntur magni dolores eos qui ratio ne voluptatem sequi nesciunt. Neque porro quisquam est, qui dolorem ipsum quia dolor sit amet, consectetur</p>
    <h5>- Owen Calloway</h5>
  </article>
</section>

<section class="blog">
  <h2 class="section-title light" style="top:4282px">LATEST BLOG</h2>
  <article class="blog-card" style="left:171px">
    <div class="blog-img" role="img" aria-label="Photo of colleagues shaking hands across a desk"></div>
    <h4>NEMO ENIM IPSAM</h4>
    <p>Sed ut perspiciatis unde omnis iste natus error sit voluptatem accusantium dolorem que laudantium, totam rem aperiam,</p>
    <a class="btn-solid">READ MORE</a>
  </article>
  <article class="blog-card" style="left:461px">
    <div class="blog-img" role="img" aria-label="Photo of a team meeting around a table"></div>
    <h4>NEMO ENIM IPSAM</h4>
    <p>Sed ut perspiciatis unde omnis iste natus error sit voluptatem accusantium dolorem que laudantium, totam rem aperiam,</p>
    <a class="btn-solid">READ MORE</a>
  </article>
  <article class="blog-card" style="left:751px">
    <div class="blog-img" role="img" aria-label="Photo of a cheering office team"></div>
    <h4>NEMO ENIM IPSAM</h4>
    <p>Sed ut perspiciatis unde omnis iste natus error sit voluptatem accusantium dolorem que laudantium, totam rem aperiam,</p>
    <a class="btn-solid">READ MORE</a>
  </article>
</section>

<footer class="footer">
  <div class="brand">Brightmoor<br>Talent</div>
  <div class="foot-col" style="left:429px">
    <h6>RECENT POSTS</h6>
    <div class="post"><b>Nemo enim ipsam voluptatem quia voluptas</b><span>June 15, 2019</span></div>
    <div class="post"><b>Nemo enim ipsam voluptatem quia voluptas</b><span>June 15, 2019</span></div>
    <div class="post"><b>Nemo enim ipsam voluptatem quia voluptas</b><span>June 15, 2019</span></div>
  </div>
  <div class="foot-col" style="left:662px">
    <h6>QUICK LINKS</h6>
    <ul class="links"><li>Home</li><li>About</li><li>Blog</li><li>Services</li><li>Jobs</li><li>Contact</li></ul>
  </div>
  <div class="foot-col" style="left:831px">
    <h6>CONTACT US</h6>
    <div class="contact-row"><i><svg width="12" height="14" viewBox="0 0 12 14" fill="none" stroke="#0b4fa3" stroke-width="1.6"><path d="M6 13s5-5 5-8a5 5 0 0 0-10 0c0 3 5 8 5 8z"/><circle cx="6" cy="5" r="1.6"/></svg></i><span>48 Harbour Lane, Westfield, VIC 3150</span></div>
    <div class="contact-row"><i><svg width="14" height="14" viewBox="0 0 14 14" fill="none" stroke="#0b4fa3" stroke-width="1.6"><path d="M3 1h3l1 3-2 1.5a8 8 0 0 0 3.5 3.5L10 7l3 1v3a2 2 0 0 1-2 2A10 10 0 0 1 1 3a2 2 0 0 1 2-2z"/></svg></i><span>(03) 5550 1247<br>(03) 5550 8832</span></div>
    <div class="contact-row"><i><svg width="14" height="12" viewBox="0 0 14 12" fill="none" stroke="#0b4fa3" stroke-width="1.6"><rect x="1" y="1" width="12" height="10" rx="1"/><path d="M1 2l6 5 6-5"/></svg></i><span>Mail:<br>info@brightmoortalent.com</span></div>
  </div>
  <div class="copyright">Copyrights @ 2022 Brightmoor Talent.</div>
</footer>

</body>
</html>
```